Simple Logo Design for Semi-Clear Plastic Frosted Card stock

Create a business card on frosted plastic. compliment existing logo elements with a tree trunk, roots, or seed at the lower half and the full logo both on the front.

Contact information will go on a solid portion of the back of this design since this card stock is semi-transparent.

It is important to consider this plastic card stock medium in your design. I found helpful tips and guides listed at vellaprint-sample.net: be careful to understand ink printed on plastic cards cannot have too much of a consistent print area or risks peeling and fine lines can easily scratch off.
Updates

2" x 3.5" 20PT Clear Plastic Business cards with Round corners Please get info or templates here: https://www.vellaprint-sample.net/product-detail/2-x-35-20pt-clear-plastic-business-cards-with-round-corners

Target Market(s)

Not for profit- religion

Industry/Entity Type

Business

Must include complementary elements to the existing logo

Font styles to use
Decorative

Colors
000000

Requirements
Must have
• Elements of community, nature and oneness. Such as: seed, roots, tree trunk, etc.
• Three lines of space on the back for Name, Title, Phone Number.
Nice to have
• I like a light use of decorative elements
Should not have
• No eyes, from faces or animals.

```html
<!DOCTYPE html>
<html lang="en">
<head>
<meta charset="utf-8">
<title>Rooted Way – Frosted Business Card</title>
<link rel="stylesheet" href="https://fonts.googleapis.com/css2?family=Questrial&family=Roboto:wght@400;700&display=swap">
<style>
  :root {
    --backdrop: #d8d3cb;
    --frost-top: #f1f2ef;
    --frost-bottom: #e2e5e1;
    --teal: #2b6b67;
    --teal-deep: #235c58;
    --leaf: #4f9a3e;
    --ink: #3b4644;
    --rule: #6d9a4a;
    --arc-grey: #b9bdbb;
  }
  * { margin: 0; padding: 0; box-sizing: border-box; }
  html, body {
    width: 969px;
    height: 1200px;
    overflow: hidden;
    background: var(--backdrop);
  }
  .canvas {
    position: relative;
    width: 969px;
    height: 1200px;
  }
  .card {
    position: absolute;
    left: 204px;
    top: 110px;
    width: 560px;
    height: 980px;
    border-radius: 22px;
    overflow: hidden;
    background: linear-gradient(180deg, var(--frost-top), var(--frost-bottom));
    box-shadow: 0 10px 30px rgba(0,0,0,0.12);
    font-family: "Questrial", "Century Gothic", sans-serif;
    color: var(--ink);
    text-align: center;
  }
  .brand-mark {
    position: absolute;
    left: 50%;
    top: 88px;
    width: 130px;
    height: 130px;
    margin-left: -65px;
    border-radius: 50%;
    background: var(--teal);
  }
  .brand-name {
    position: absolute;
    top: 240px;
    left: 0;
    width: 100%;
    font-size: 52px;
    font-weight: 400;
    letter-spacing: 1px;
    color: var(--teal);
    line-height: 1;
  }
  .brand-tagline {
    position: absolute;
    top: 300px;
    left: 0;
    width: 100%;
    font-size: 17px;
    letter-spacing: 2px;
    color: var(--ink);
  }
  .brand-rule {
    position: absolute;
    top: 336px;
    left: 70px;
    width: 420px;
    height: 2px;
    background: linear-gradient(90deg, transparent, var(--rule) 20%, var(--rule) 80%, transparent);
  }
  .motto {
    position: absolute;
    top: 362px;
    left: 0;
    width: 100%;
    font-size: 22px;
    letter-spacing: 0.5px;
  }
  .contact { position: absolute; left: 0; width: 100%; }
  .contact-name {
    top: 446px;
    font-family: "Roboto", "Arial", sans-serif;
    font-weight: 700;
    font-size: 33px;
    letter-spacing: 1px;
    color: var(--teal);
  }
  .contact-title {
    top: 492px;
    font-family: "Roboto", "Arial", sans-serif;
    font-size: 24px;
    letter-spacing: 0.5px;
  }
  .contact-phone {
    top: 547px;
    font-family: "Roboto", "Arial", sans-serif;
    font-size: 23px;
  }
  .ground {
    position: absolute;
    left: 0;
    top: 610px;
    width: 560px;
    height: 370px;
  }
</style>
</head>
<body>
<main class="canvas">
  <section class="card">
    <span class="brand-mark" aria-hidden="true"></span>
    <h1 class="brand-name">ROOTEDWAY</h1>
    <p class="brand-tagline">WISDOM, FELLOWSHIP &amp; CALM</p>
    <span class="brand-rule" aria-hidden="true"></span>
    <p class="motto">TOGETHER AS ONE COMMUNITY</p>
    <p class="contact contact-name">JORDAN WHITFIELD</p>
    <p class="contact contact-title">General Manager</p>
    <p class="contact contact-phone">+555-014-2290</p>

    <svg class="ground" viewBox="0 0 560 370" xmlns="http://www.w3.org/2000/svg">
      <defs>
        <linearGradient id="canopy" x1="0" y1="0" x2="0" y2="1">
          <stop offset="0" stop-color="#2b6b67"/>
          <stop offset="0.45" stop-color="#4f9a3e"/>
          <stop offset="0.7" stop-color="#2b6b67"/>
          <stop offset="1" stop-color="#235c58"/>
        </linearGradient>
      </defs>
      <path class="ground-arc" d="M0 40 Q280 -20 560 40" fill="none" stroke="#b9bdbb" stroke-width="10"/>
      <path d="M0 52 Q280 -6 560 52 L560 370 L0 370 Z" fill="url(#canopy)"
            role="img" aria-label="Illustration of a leafy tree canopy over a spreading trunk and roots"/>
    </svg>
  </section>
</main>
</body>
</html>
```